Communication and Marketing agency needs a new presentation card

We are a group of communication and marketing agencies specialized in companies that are in the logistics and industrial sector. The head agency is TELVANO Grupo and the group consists of 4 agencies: TELVANO Media, TELVANO Digital, TELVANO Research and DifundeEnPantalla. We hace 4 offices in Spain (Madrid, Barcelona, Valencia and Murcia). We are looking for a clean and attractive design that transmits our experience, brand presence in the market and knowledge to those who receive the card.It has to maintain the colors of the logo that is attached.
Target Market(s)
logistics and industrial sector
Marketing department
Contact Information for Business Card
Clean and attractive design

```html
<!DOCTYPE html>
<html lang="es">
<head>
<meta charset="utf-8">
<title>TELVANO Grupo – Tarjeta de presentación</title>
<link rel="stylesheet" href="https://fonts.googleapis.com/css2?family=Montserrat:wght@400;500;600;700&display=swap">
<style>
  :root{
    --bg:#1b1f23;
    --card-dark:#2b2826;
    --card-light:#ffffff;
    --brand-red:#b3172b;
    --ink:#2a2a2a;
    --ink-soft:#555;
    --light-text:#f2f2f2;
    --map-grey:#9a9a9a;
  }
  *{margin:0;padding:0;box-sizing:border-box}
  html,body{width:1200px;height:738px;overflow:hidden;background:var(--bg)}
  body{font-family:"Montserrat",sans-serif;position:relative}
  .card{position:absolute;width:540px;height:310px;top:214px;border-radius:3px;box-shadow:0 12px 30px rgba(0,0,0,.5)}
  .card--back{left:40px;background:var(--card-dark)}
  .card--front{left:620px;background:var(--card-light)}

  /* back: agency names */
  .agency-grid{position:absolute;left:70px;top:95px;width:400px;display:grid;grid-template-columns:1fr 1fr;row-gap:42px;column-gap:30px}
  .agency{font-weight:600;font-size:21px;letter-spacing:.5px;line-height:1}
  .agency--red{color:var(--brand-red)}
  .agency--white{color:var(--light-text)}
  .agency small{display:block;font-size:12px;margin-top:5px;text-align:right}

  /* front */
  .group-name{position:absolute;right:26px;top:26px;color:var(--brand-red);font-weight:600;font-size:30px;letter-spacing:.5px;text-align:right;line-height:1}
  .group-name small{display:block;font-size:16px;margin-top:4px}
  .person{position:absolute;left:26px;top:142px;padding-left:18px}
  .person__bars{position:absolute;left:0;top:2px;width:10px;height:30px;display:flex;gap:2px}
  .person__bars span{display:block;height:100%}
  .person__bars span:first-child{width:6px;background:var(--ink)}
  .person__bars span:last-child{width:2px;background:var(--brand-red)}
  .person__name{color:var(--brand-red);font-size:18px;font-weight:400;line-height:1}
  .person__name b{font-weight:700}
  .person__role{font-size:12px;color:var(--ink);margin-top:5px}
  .contact{position:absolute;left:44px;top:205px;list-style:none;font-size:13px;color:var(--ink);line-height:19px}
  .contact li{display:flex;align-items:center;gap:9px}
  .contact svg{width:9px;height:9px;flex:none}
  .map{position:absolute;right:40px;top:110px;width:190px;height:115px;background:radial-gradient(ellipse at center,#b9b9b9 0%,#dedede 70%,#fff 100%);border-radius:20px}
  .offices{position:absolute;right:26px;top:240px;font-size:11px;font-weight:600;color:var(--ink)}
  .offices span{color:var(--brand-red);margin:0 3px}
</style>
</head>
<body>
  <section class="card card--back" aria-label="Reverso de la tarjeta">
    <div class="agency-grid">
      <div class="agency agency--red">TELVANO <small>Media</small></div>
      <div class="agency agency--white">TELVANO <small>Research</small></div>
      <div class="agency agency--white">TELVANO <small>Digital</small></div>
      <div class="agency agency--red">DifundeEnPantalla</div>
    </div>
  </section>

  <section class="card card--front" aria-label="Anverso de la tarjeta">
    <div class="group-name">TELVANO <small>Grupo</small></div>

    <div class="person">
      <div class="person__bars"><span></span><span></span></div>
      <p class="person__name"><b>Lorenzo</b> Arrieta</p>
      <p class="person__role">Director</p>
    </div>

    <ul class="contact">
      <li><svg viewBox="0 0 10 10"><path d="M2 1l2 2-1 1.2a6 6 0 0 0 2.8 2.8L7 6l2 2-1.3 1.3C4.5 9 1 5.5.7 2.3z" fill="var(--brand-red)"/></svg>910 472 318</li>
      <li><svg viewBox="0 0 10 10"><rect x="2.5" y=".5" width="5" height="9" rx="1" fill="none" stroke="var(--brand-red)" stroke-width="1.2"/></svg>655 201 487</li>
      <li><svg viewBox="0 0 10 10"><rect x=".6" y="2" width="8.8" height="6" fill="none" stroke="var(--brand-red)" stroke-width="1.1"/><path d="M.6 2L5 5.5 9.4 2" fill="none" stroke="var(--brand-red)" stroke-width="1.1"/></svg>larrieta@telvano.es</li>
      <li><svg viewBox="0 0 10 10"><circle cx="5" cy="5" r="4.2" fill="none" stroke="var(--brand-red)" stroke-width="1.1"/><path d="M.8 5h8.4M5 .8c-2.4 2.6-2.4 5.8 0 8.4M5 .8c2.4 2.6 2.4 5.8 0 8.4" fill="none" stroke="var(--brand-red)" stroke-width=".8"/></svg>www.telvano.es</li>
      <li><svg viewBox="0 0 10 10"><rect x="1" y="1" width="8" height="8" fill="var(--brand-red)"/></svg>lorenzoarrieta</li>
    </ul>

    <div class="map" role="img" aria-label="Mapa punteado de España con las oficinas marcadas"></div>
    <p class="offices">Madrid<span>|</span>Barcelona<span>|</span>Valencia<span>|</span>Murcia</p>
  </section>
</body>
</html>
```